Redesign of business card for Cedar Ridge Mechanical

We are looking for a new design for our business cards for Cedar Ridge Mechanical. We are a plumbing & HVAC construction company, operating on the West Coast of Canada and USA. Logo attached.
Industry/Entity Type
Construction - Plumbing & HVAC
Contact Information for Business Card
Name, address, phone numbers, email, website address
Look and feel
Each slider illustrates characteristics of the customer's brand and the style your logo design should communicate.

```html
<!DOCTYPE html>
<html lang="en">
<head>
<meta charset="utf-8">
<title>Cedar Ridge Mechanical – Business Card</title>
<link href="https://fonts.googleapis.com/css2?family=Montserrat:wght@400;500;700&family=Oswald:wght@500&display=swap" rel="stylesheet">
<style>
  :root {
    --stage: #262626;
    --card-white: #ffffff;
    --ink: #1f1f1f;
    --charcoal: #2b2b2b;
    --mid-grey: #9a9a9a;
    --soft-grey: #7a7a7a;
    --back-black: #141414;
    --back-sheen: #2a2a2a;
    --paper-text: #f4f4f4;
  }
  * { margin: 0; padding: 0; box-sizing: border-box; }
  html, body { width: 1200px; height: 801px; overflow: hidden; }
  body {
    background: var(--stage);
    font-family: "Montserrat", sans-serif;
    position: relative;
  }
  .card {
    position: absolute;
    top: 246px;
    width: 540px;
    height: 309px;
    border-radius: 22px;
    overflow: hidden;
    box-shadow: 0 18px 40px rgba(0,0,0,0.45);
  }
  .card-front { left: 40px; background: var(--card-white); }
  .card-back { left: 620px; background: var(--back-black); }

  .front-wave { position: absolute; inset: 0; }

  .brand {
    position: absolute;
    left: 38px;
    top: 108px;
    display: flex;
    align-items: center;
    gap: 12px;
  }
  .brand-square { width: 30px; height: 30px; background: var(--ink); }
  .brand-name {
    font-weight: 700;
    font-size: 19px;
    color: var(--ink);
    letter-spacing: 0.3px;
  }

  .address {
    position: absolute;
    left: 40px;
    top: 188px;
    font-size: 14px;
    line-height: 1.4;
    color: var(--soft-grey);
  }

  .person {
    position: absolute;
    right: 26px;
    top: 22px;
    text-align: right;
  }
  .person-name {
    font-size: 17px;
    font-weight: 700;
    color: var(--ink);
    letter-spacing: 0.5px;
  }
  .person-name .surname { color: var(--mid-grey); }
  .person-role { font-size: 12px; color: var(--ink); margin-top: 2px; }

  .contacts {
    position: absolute;
    right: 24px;
    top: 178px;
    list-style: none;
    text-align: right;
  }
  .contacts li {
    display: flex;
    justify-content: flex-end;
    align-items: center;
    gap: 8px;
    font-size: 12.5px;
    color: var(--paper-text);
    line-height: 22px;
  }
  .contacts svg { width: 12px; height: 12px; flex: none; }

  .back-field {
    position: absolute;
    inset: 0;
    background: linear-gradient(150deg, var(--back-sheen) 0%, var(--back-black) 45%, var(--back-sheen) 100%);
  }
  .back-name {
    position: absolute;
    left: 0; right: 0;
    top: 128px;
    text-align: center;
    font-family: "Oswald", sans-serif;
    font-weight: 500;
    font-size: 36px;
    letter-spacing: 3px;
    color: var(--paper-text);
  }
</style>
</head>
<body>

<section class="card card-front">
  <svg class="front-wave" viewBox="0 0 540 309" aria-hidden="true">
    <path d="M540,72 C415,78 350,115 310,178 C270,245 190,292 40,309 L90,309 C200,295 280,245 320,185 C360,125 420,94 540,90 Z" fill="#9a9a9a"/>
    <path d="M540,90 C420,94 360,125 320,185 C280,245 200,295 90,309 L540,309 Z" fill="#2b2b2b"/>
    <path d="M540,82 C418,86 355,120 315,182" fill="none" stroke="#d0d0d0" stroke-width="1.2"/>
  </svg>

  <div class="brand">
    <span class="brand-square"></span>
    <span class="brand-name">Cedar Ridge Mechanical</span>
  </div>

  <p class="address">Your address, city<br>state, ZIP 0000</p>

  <div class="person">
    <p class="person-name">DANIEL <span class="surname">REYES</span></p>
    <p class="person-role">Manager</p>
  </div>

  <ul class="contacts">
    <li>123-456-2100
      <svg viewBox="0 0 12 12"><path d="M3 1 L5 3.5 L4 4.8 C4.6 6 5.9 7.4 7.2 8 L8.5 7 L11 9 L9.8 11 C5.5 10.6 1.4 6.5 1 2.2 Z" fill="#f4f4f4"/></svg>
    </li>
    <li>hello@cedarridgemech.com
      <svg viewBox="0 0 12 12"><rect x="1" y="2.5" width="10" height="7" fill="#f4f4f4"/><path d="M1 2.5 L6 6.5 L11 2.5" fill="none" stroke="#2b2b2b" stroke-width="1"/></svg>
    </li>
    <li>www.cedarridgemech.com
      <svg viewBox="0 0 12 12"><circle cx="6" cy="6" r="5" fill="#f4f4f4"/><path d="M1 6 H11 M6 1 C3.5 3.5 3.5 8.5 6 11 M6 1 C8.5 3.5 8.5 8.5 6 11" fill="none" stroke="#2b2b2b" stroke-width="0.8"/></svg>
    </li>
  </ul>
</section>

<section class="card card-back">
  <div class="back-field" role="img" aria-label="Glossy spot-varnish brand pattern across the card back"></div>
  <p class="back-name">CEDAR RIDGE MECHANICAL</p>
</section>

</body>
</html>
```